Innovative cost reduction consultant needs to build a group of technical advisors

We need to share our message and compassion for developing cost reduction in the automotive industry. We create opportunities for immediate innovation, by developing cost reduction solutions across suppliers with related process. Attached is an existing Power Point, but it needs improvement. Most of all, a good compelling story, why experts should join us.

Target Market(s)

Automotive industry, supply chain management

Industry/Entity Type

Automotive

Font styles to use
Serif
Sans Serif

Requirements
Must have
• Better visual graphics. There are a few, but they are not as visually appearing as I would like. A graphic with data should have a better visual impact then the ones that I created. I would like to share the message, that I am providing a solution for the automotive industry. The goal is to reduce costs and improve supplier and OEM relationships. The objective is to do so by creating opportunities for immediate innovation, by developing cost reduction solutions across suppliers with related processes. This message may need a visual graphic, which is missing from the presentation.
Nice to have
• Challenge my story and presentation. Does this make sense to you, and what is your opinions of the subject. Or, a relevant news source to validate the story.
Should not have
• I have not decided on the name of the venture or logo. So, let's just use my name as the source or writer. Marcus Delby, Cost Reduction Specialist. Thanks,

```html
<!DOCTYPE html>
<html lang="en">
<head>
<meta charset="utf-8">
<title>Business Model</title>
<link href="https://fonts.googleapis.com/css2?family=Roboto+Condensed:wght@300;400;700&display=swap" rel="stylesheet">
<style>
  :root {
    --band-dark: #0b4a9a;
    --band-mid: #1460b6;
    --band-light: #2a9be0;
    --stripe: #d6d6d6;
    --stripe-bg: #ffffff;
    --text-white: #ffffff;
    --blue: #1a76d0;
    --blue-dark: #0d4d9c;
    --green: #4bb13b;
    --green-dark: #237a22;
    --orange: #f08a1c;
    --orange-dark: #c55a07;
    --purple: #9b2fa8;
    --purple-dark: #5f1470;
    --brown: #a0642b;
    --brown-dark: #6a3c14;
    --red: #e0222a;
    --red-dark: #9a0d14;
    --navy: #1b48a8;
    --navy-dark: #0c2a6e;
    --magenta: #8e1c6a;
    --magenta-dark: #520b3c;
    --teal: #1ea58d;
    --teal-dark: #0b6a5c;
  }
  * { margin: 0; padding: 0; box-sizing: border-box; }
  html, body { width: 1200px; height: 650px; overflow: hidden; background: #fff; }
  .slide {
    position: relative;
    width: 1200px;
    height: 650px;
    overflow: hidden;
    font-family: "Roboto Condensed", "Arial Narrow", sans-serif;
    background:
      linear-gradient(90deg, rgba(255,255,255,0) 38%, rgba(150,150,150,0.75) 100%),
      repeating-linear-gradient(180deg, var(--stripe-bg) 0 9px, var(--stripe) 9px 13px);
  }
  .title-band {
    position: absolute;
    left: 0; top: 0;
    width: 1200px; height: 97px;
    background: linear-gradient(180deg, var(--band-mid) 0%, var(--band-dark) 100%);
    border-bottom: 4px solid #fff;
  }
  .title-band h1 {
    position: absolute;
    left: 80px; top: 44px;
    color: var(--text-white);
    font-weight: 700;
    font-size: 46px;
    letter-spacing: -0.5px;
    line-height: 1;
  }
  .footer-band {
    position: absolute;
    left: 0; bottom: 0;
    width: 1200px; height: 26px;
    background: linear-gradient(90deg, var(--band-light), #49b0ec);
  }
  .footer-gap {
    position: absolute;
    left: 0; bottom: 26px;
    width: 1200px; height: 28px;
    background: linear-gradient(90deg, #fff 40%, #d4d4d4 100%);
  }
  .block {
    position: absolute;
    color: var(--text-white);
    text-align: center;
    border-radius: 50% 50% 50% 50% / 72% 72% 14% 14%;
    box-shadow: 0 16px 14px -8px rgba(0,0,0,0.35), inset -10px -14px 24px rgba(0,0,0,0.25);
  }
  .block h2 {
    font-size: 22px;
    font-weight: 700;
    line-height: 27px;
    text-shadow: 0 1px 2px rgba(0,0,0,0.35);
  }
  .block p {
    font-size: 16.5px;
    font-weight: 300;
    line-height: 23px;
    white-space: nowrap;
  }
  .badge {
    position: absolute;
    width: 44px; height: 44px;
    border-radius: 50%;
    border: 3px solid #fff;
    box-shadow: 0 2px 4px rgba(0,0,0,0.3);
  }
  .badge svg { width: 100%; height: 100%; display: block; }

  .key-partners { left: 70px; top: 201px; width: 223px; height: 175px; padding-top: 15px; background: radial-gradient(circle at 35% 25%, var(--blue), var(--blue-dark) 85%); z-index: 4; }
  .key-activities { left: 261px; top: 144px; width: 221px; height: 175px; padding-top: 17px; background: radial-gradient(circle at 35% 25%, var(--green), var(--green-dark) 85%); z-index: 1; }
  .value-proposition { left: 448px; top: 229px; width: 244px; height: 191px; padding-top: 27px; background: radial-gradient(circle at 35% 25%, var(--orange), var(--orange-dark) 85%); z-index: 5; }
  .customer-relationships { left: 634px; top: 138px; width: 227px; height: 187px; padding-top: 26px; background: radial-gradient(circle at 35% 25%, var(--purple), var(--purple-dark) 85%); z-index: 2; }
  .customer-segments { left: 848px; top: 178px; width: 268px; height: 204px; padding-top: 19px; background: radial-gradient(circle at 35% 25%, var(--brown), var(--brown-dark) 85%); z-index: 3; }
  .key-resources { left: 182px; top: 331px; width: 223px; height: 172px; padding-top: 22px; background: radial-gradient(circle at 35% 25%, var(--red), var(--red-dark) 85%); z-index: 7; }
  .channels { left: 376px; top: 420px; width: 216px; height: 172px; padding-top: 28px; background: radial-gradient(circle at 35% 25%, var(--navy), var(--navy-dark) 85%); z-index: 9; }
  .cost-structure { left: 580px; top: 382px; width: 223px; height: 179px; padding-top: 14px; background: radial-gradient(circle at 35% 25%, var(--magenta), var(--magenta-dark) 85%); z-index: 8; }
  .revenue-streams { left: 777px; top: 347px; width: 210px; height: 163px; padding-top: 28px; background: radial-gradient(circle at 35% 25%, var(--teal), var(--teal-dark) 85%); z-index: 6; }

  .key-partners p { margin-top: 7px; }
  .key-activities p { margin-top: 5px; }
  .value-proposition p { margin-top: 9px; }
  .customer-relationships p { margin-top: 10px; }
  .customer-segments p { margin-top: 2px; }
  .key-resources p { margin-top: 5px; }
  .channels p { margin-top: 5px; }
  .cost-structure p { margin-top: 7px; }
  .revenue-streams p { margin-top: 5px; }

  .key-partners .badge { left: 14px; top: 6px; background: var(--blue); }
  .key-activities .badge { left: 7px; top: 3px; background: var(--green); }
  .value-proposition .badge { left: 18px; top: 17px; background: var(--orange); }
  .customer-relationships .badge { left: 3px; top: 32px; background: var(--purple); }
  .customer-segments .badge { left: 24px; top: 11px; background: var(--brown); }
  .key-resources .badge { left: 4px; top: 6px; background: var(--red); }
  .channels .badge { left: 3px; top: 13px; background: var(--navy); }
  .cost-structure .badge { left: 4px; top: 16px; background: var(--magenta); }
  .revenue-streams .badge { left: 4px; top: 13px; background: var(--teal); }
</style>
</head>
<body>
<main class="slide">
  <header class="title-band"><h1>Business Model</h1></header>

  <section class="block key-activities">
    <span class="badge"><svg viewBox="0 0 44 44"><path d="M12 23 l7 7 l13 -14" fill="none" stroke="#fff" stroke-width="5" stroke-linecap="round" stroke-linejoin="round"/></svg></span>
    <h2>Key<br>Activities</h2><p>Supplier Survey<br>Analysis</p>
  </section>

  <section class="block customer-relationships">
    <span class="badge"><svg viewBox="0 0 44 44"><path d="M22 32 C10 24 10 14 16 13 C19 12.5 21 14 22 16 C23 14 25 12.5 28 13 C34 14 34 24 22 32 Z" fill="#fff"/></svg></span>
    <h2>Customer<br>Relationships</h2><p>Cost Reduction,<br>Supplier Dashboard</p>
  </section>

  <section class="block customer-segments">
    <span class="badge"><svg viewBox="0 0 44 44" fill="#fff"><circle cx="22" cy="16" r="4.5"/><circle cx="13" cy="18" r="3.5"/><circle cx="31" cy="18" r="3.5"/><path d="M14 30 a8 8 0 0 1 16 0 z"/><path d="M6 30 a7 7 0 0 1 11 -5 a10 10 0 0 0 -2 5 z"/><path d="M38 30 a7 7 0 0 0 -11 -5 a10 10 0 0 1 2 5 z"/></svg></span>
    <h2>Customer<br>Segments</h2><p>OEM<br>Suppliers<br>Supply Chain Management</p>
  </section>

  <section class="block key-partners">
    <span class="badge"><svg viewBox="0 0 44 44" fill="none" stroke="#fff" stroke-width="3.5" stroke-linecap="round"><path d="M20 24 l-5 5 a4 4 0 0 1 -6 -6 l5 -5 a4 4 0 0 1 6 0"/><path d="M24 20 l5 -5 a4 4 0 0 1 6 6 l-5 5 a4 4 0 0 1 -6 0"/><path d="M18 26 l8 -8"/></svg></span>
    <h2>Key<br>Partners</h2><p>Advisors, R&amp;D Industry,<br>Supply Chain Consultants</p>
  </section>

  <section class="block value-proposition">
    <span class="badge"><svg viewBox="0 0 44 44" fill="#fff"><rect x="11" y="18" width="22" height="5"/><rect x="13" y="24" width="18" height="10"/><rect x="20.5" y="18" width="3" height="16" fill="#f08a1c"/><path d="M22 18 c-3 -6 -9 -4 -6 0 z M22 18 c3 -6 9 -4 6 0 z"/></svg></span>
    <h2>Value<br>Proposition</h2><p>Cost Reduction,<br>OEM &amp; Supplier<br>relationship</p>
  </section>

  <section class="block revenue-streams">
    <span class="badge"><svg viewBox="0 0 44 44"><path d="M18 12 h8 l-2 4 c6 3 9 8 9 13 c0 4 -4 5 -11 5 s-11 -1 -11 -5 c0 -5 3 -10 9 -13 z" fill="#fff"/><text x="22" y="31" text-anchor="middle" font-family="Roboto Condensed, sans-serif" font-weight="700" font-size="12" fill="#1ea58d">$</text></svg></span>
    <h2>Revenue<br>Streams</h2><p>Innovation Integration<br>Data Analysis</p>
  </section>

  <section class="block key-resources">
    <span class="badge"><svg viewBox="0 0 44 44" fill="#fff"><path d="M10 32 v-12 l6 4 v-4 l6 4 v-4 l6 4 v-10 h5 v18 z"/><rect x="14" y="27" width="3" height="3" fill="#e0222a"/><rect x="20" y="27" width="3" height="3" fill="#e0222a"/><rect x="26" y="27" width="3" height="3" fill="#e0222a"/></svg></span>
    <h2>Key<br>Resources</h2><p>Advisors<br>R&amp;D Industry</p>
  </section>

  <section class="block cost-structure">
    <span class="badge"><svg viewBox="0 0 44 44"><path d="M12 22 l10 -10 h9 v9 l-10 10 z" fill="#fff"/><circle cx="27" cy="17" r="2" fill="#8e1c6a"/></svg></span>
    <h2>Cost<br>Structure</h2><p>Conceptual Model<br>Dashboard Maintenance<br>Supplier Survey Analysis</p>
  </section>

  <section class="block channels">
    <span class="badge"><svg viewBox="0 0 44 44" fill="#fff"><rect x="9" y="15" width="16" height="12"/><path d="M26 19 h5 l4 5 v3 h-9 z"/><circle cx="14" cy="29" r="3"/><circle cx="30" cy="29" r="3"/></svg></span>
    <h2>Channels</h2><p>Supply Chain<br>Management<br>Partnerships,<br>Direct Sales</p>
  </section>

  <div class="footer-gap"></div>
  <footer class="footer-band"></footer>
</main>
</body>
</html>
```